Small Business Broker Business Card Design

A business card design for a small business brokerage, which is a financial service, not unlike real estate brokerage, but for small businesses such as laundromats, pizza shops, restaurants, cleaners etc. The designs should all be simple, more conservative in nature, using the colors and font of the logo. Again, think real estate Brokerage as a business context
Contact Information for Business Card
Name: Glen R. Harlow. Title: Small Business Advisor. Email: g.harlow@bayfieldcapitalworks.example. Mobile: (555) 274-3918. Office: (555) 806-2147. www.bayfieldcapitalworks.example

```html
<!DOCTYPE html>
<html lang="en">
<head>
<meta charset="UTF-8">
<title>Bayfield Capital Works – Business Card</title>
<link rel="stylesheet" href="https://fonts.googleapis.com/css2?family=Montserrat:wght@600;700&family=Arimo:wght@400&display=swap">
<style>
  :root {
    --navy: #1b3a6a;
    --navy-light: #26477a;
    --green: #8dc63f;
    --white: #ffffff;
    --ink: #333333;
    --backdrop: #dcdcdc;
  }
  * { margin: 0; padding: 0; box-sizing: border-box; }
  html, body {
    width: 1200px; height: 900px; overflow: hidden;
    background: var(--backdrop);
  }
  .canvas {
    width: 1200px; height: 900px;
    display: flex; flex-direction: column; align-items: center; justify-content: center;
    gap: 36px;
  }
  .card {
    position: relative;
    width: 700px; height: 400px;
    border-radius: 22px;
    overflow: hidden;
    box-shadow: 0 6px 18px rgba(0,0,0,0.18);
  }

  /* Front */
  .card-front {
    background: linear-gradient(160deg, var(--navy-light) 0%, var(--navy) 55%, var(--navy) 100%);
  }
  .front-brand {
    position: absolute; inset: 0;
    display: flex; flex-direction: column; align-items: center; justify-content: center;
    gap: 14px;
  }
  .front-brand .brand-row { display: flex; align-items: center; gap: 16px; }
  .front-brand .brand-square { width: 22px; height: 22px; background: var(--green); flex: none; }
  .front-brand .brand-name {
    font-family: 'Montserrat', sans-serif; font-weight: 700;
    color: var(--white); font-size: 30px; letter-spacing: 1.5px; text-transform: uppercase;
    white-space: nowrap;
  }
  .front-brand .tagline {
    font-family: 'Montserrat', sans-serif; font-weight: 600;
    color: var(--green); font-size: 14px; letter-spacing: 3.2px; text-transform: uppercase;
    white-space: nowrap;
  }

  /* Back */
  .card-back { background: var(--white); }
  .back-brand {
    position: absolute; left: 56px; top: 170px;
    display: flex; align-items: center; gap: 14px;
  }
  .back-brand .brand-square { width: 18px; height: 18px; background: var(--green); flex: none; }
  .back-brand .brand-name {
    font-family: 'Montserrat', sans-serif; font-weight: 700;
    color: var(--navy); font-size: 20px; letter-spacing: 1px; text-transform: uppercase;
    line-height: 1.25;
  }
  .contact-block {
    position: absolute; left: 360px; top: 96px; width: 320px;
  }
  .person-name {
    font-family: 'Montserrat', sans-serif; font-weight: 700;
    font-size: 27px; letter-spacing: 1px; text-transform: uppercase;
    color: var(--navy); white-space: nowrap;
  }
  .person-name .surname { color: var(--green); }
  .person-title {
    font-family: 'Arimo', sans-serif; font-size: 15px; color: var(--ink);
    margin-top: 2px;
  }
  .contact-list { list-style: none; margin-top: 22px; }
  .contact-list li {
    display: flex; align-items: center; gap: 10px;
    font-family: 'Arimo', sans-serif; font-size: 13px; color: var(--ink);
    line-height: 1; margin-bottom: 10px; white-space: nowrap;
  }
  .contact-list svg { width: 13px; height: 13px; flex: none; }
</style>
</head>
<body>
<main class="canvas">

  <section class="card card-front" aria-label="Card front">
    <div class="front-brand">
      <div class="brand-row">
        <span class="brand-square"></span>
        <span class="brand-name">Bayfield Capital Works, Inc</span>
      </div>
      <p class="tagline">Confidently buy or sell a local business today</p>
    </div>
  </section>

  <section class="card card-back" aria-label="Card back">
    <div class="back-brand">
      <span class="brand-square"></span>
      <span class="brand-name">Bayfield<br>Capital Works</span>
    </div>
    <div class="contact-block">
      <h1 class="person-name">Glen R. <span class="surname">Harlow</span></h1>
      <p class="person-title">Small Business Advisor</p>
      <ul class="contact-list">
        <li>
          <svg viewBox="0 0 16 16" aria-hidden="true"><path d="M2 5c0-2 2-3 6-3s6 1 6 3v1h-3V5H5v1H2zM3 8h10l1 6H2z" fill="var(--green)"/></svg>
          (555) 806-2147
        </li>
        <li>
          <svg viewBox="0 0 16 16" aria-hidden="true"><rect x="4" y="1" width="8" height="14" rx="1.5" fill="none" stroke="var(--green)" stroke-width="1.6"/><circle cx="8" cy="12.5" r="0.9" fill="var(--green)"/></svg>
          (555) 274-3918
        </li>
        <li>
          <svg viewBox="0 0 16 16" aria-hidden="true"><rect x="1" y="3" width="14" height="10" fill="var(--green)"/><path d="M1 3l7 6 7-6" fill="none" stroke="var(--white)" stroke-width="1.2"/></svg>
          g.harlow@bayfieldcapitalworks.example
        </li>
        <li>
          <svg viewBox="0 0 16 16" aria-hidden="true"><circle cx="8" cy="8" r="6.5" fill="none" stroke="var(--green)" stroke-width="1.5"/><path d="M1.5 8h13M8 1.5c-3 3-3 10 0 13M8 1.5c3 3 3 10 0 13" fill="none" stroke="var(--green)" stroke-width="1.1"/></svg>
          www.bayfieldcapitalworks.example
        </li>
      </ul>
    </div>
  </section>

</main>
</body>
</html>
```